i need a business card design for my family investment company "quorin investments" based in dubai. its a diverse investment firm focusing on education, hospitality and automotive. the design has to be modern and try to incorporate the logo "E" in the design. details on card as follow

Yusuf K Bin Tarrah
Managing Director
yusuf@quorin-mail.ae
www.quorin-mail.ae

Harbor district,palwick tower, office 4718, dubai
tel. 04 3850927
mobile.050 9184203

card used for networking events and investor meetings

Hospitality

```html
<!DOCTYPE html>
<html lang="en">
<head>
<meta charset="utf-8">
<title>Quorin Investments – Business Card</title>
<link rel="stylesheet" href="https://fonts.googleapis.com/css2?family=Josefin+Sans:wght@300;400&family=Quicksand:wght@400;700&display=swap">
<style>
  :root {
    --page-bg: #f2f3f5;
    --card-blue: #3d72b0;
    --card-ink: #ffffff;
    --card-ink-soft: rgba(255, 255, 255, 0.82);
    --divider: rgba(255, 255, 255, 0.45);
    --card-shadow: rgba(20, 35, 60, 0.22);
  }
  * { box-sizing: border-box; margin: 0; padding: 0; }
  html, body {
    width: 1200px;
    height: 1000px;
    overflow: hidden;
    background: var(--page-bg);
  }
  .sheet {
    width: 1200px;
    height: 1000px;
    display: flex;
    flex-direction: column;
    align-items: center;
    justify-content: center;
    gap: 40px;
  }
  .card {
    position: relative;
    width: 760px;
    height: 430px;
    background: var(--card-blue);
    color: var(--card-ink);
    box-shadow: 0 10px 30px var(--card-shadow);
  }

  /* wordmark */
  .wordmark {
    position: absolute;
    text-align: center;
    font-family: "Josefin Sans", sans-serif;
    font-weight: 300;
    color: var(--card-ink);
    text-transform: uppercase;
    line-height: 1;
  }
  .wordmark__name { display: block; }
  .wordmark__sub { display: block; }

  .card--front .wordmark {
    left: 0; right: 0;
    top: 52px;
    padding-left: 70px;
  }
  .card--front .wordmark__name { font-size: 44px; letter-spacing: 8px; }
  .card--front .wordmark__sub { font-size: 17px; letter-spacing: 7px; margin-top: 6px; }

  .card--back .wordmark {
    left: 0; right: 0;
    top: 150px;
  }
  .card--back .wordmark__name { font-size: 92px; letter-spacing: 16px; }
  .card--back .wordmark__sub { font-size: 28px; letter-spacing: 17px; margin-top: 14px; }

  /* person */
  .person {
    position: absolute;
    left: 44px;
    top: 200px;
    font-family: "Quicksand", sans-serif;
  }
  .person__name { font-size: 22px; font-weight: 700; letter-spacing: 0.5px; }
  .person__role { font-size: 16px; font-weight: 400; color: var(--card-ink-soft); margin-top: 6px; letter-spacing: 0.5px; }

  /* contact block */
  .contact {
    position: absolute;
    left: 450px;
    top: 170px;
    padding-left: 18px;
    border-left: 1px solid var(--divider);
    font-family: "Quicksand", sans-serif;
    font-size: 15px;
    line-height: 1.35;
    color: var(--card-ink-soft);
  }
  .contact__address { margin-bottom: 4px; }
  .contact__row { display: flex; align-items: center; gap: 6px; }
  .contact__icon { width: 14px; height: 14px; flex: none; }
</style>
</head>
<body>
<main class="sheet">

  <section class="card card--front" aria-label="Business card front">
    <div class="wordmark">
      <span class="wordmark__name">Quorin</span>
      <span class="wordmark__sub">Investments</span>
    </div>

    <div class="person">
      <p class="person__name">Yusuf K Bin Tarrah</p>
      <p class="person__role">Managing Director</p>
    </div>

    <div class="contact">
      <p class="contact__address">Harbor district, palwick tower,<br>office 4718, dubai</p>
      <p class="contact__row">
        <svg class="contact__icon" viewBox="0 0 16 16" aria-hidden="true"><path fill="#fff" d="M4 1.5l2.2 3-1.3 1.6a9 9 0 0 0 5 5l1.6-1.3 3 2.2-1.3 2.3C8.6 14.3 1.7 7.4 1.7 2.8z"/></svg>
        <span>: 04 3850927</span>
      </p>
      <p class="contact__row">
        <svg class="contact__icon" viewBox="0 0 16 16" aria-hidden="true"><rect x="4" y="1" width="8" height="14" rx="1.5" fill="none" stroke="#fff" stroke-width="1.4"/><rect x="5.5" y="3" width="5" height="6" fill="#fff"/></svg>
        <span>: 050 9184203</span>
      </p>
      <p class="contact__row">
        <svg class="contact__icon" viewBox="0 0 16 16" aria-hidden="true"><rect x="1" y="3.5" width="14" height="9" fill="#fff"/><path d="M1 3.5l7 5 7-5" fill="none" stroke="#3d72b0" stroke-width="1"/></svg>
        <span>: yusuf@quorin-mail.ae</span>
      </p>
      <p class="contact__row">
        <svg class="contact__icon" viewBox="0 0 16 16" aria-hidden="true"><circle cx="8" cy="8" r="6.5" fill="none" stroke="#fff" stroke-width="1.2"/><ellipse cx="8" cy="8" rx="3" ry="6.5" fill="none" stroke="#fff" stroke-width="1"/><path d="M1.5 8h13" stroke="#fff" stroke-width="1"/></svg>
        <span>: www.quorin-mail.ae</span>
      </p>
    </div>
  </section>

  <section class="card card--back" aria-label="Business card back">
    <div class="wordmark">
      <span class="wordmark__name">Quorin</span>
      <span class="wordmark__sub">Investments</span>
    </div>
  </section>

</main>
</body>
</html>
```